Core Value Graphic for a Service Disabled and Minority Certified contractor

My company, Keystone Aid Partners, is a US Federal Contractor that hires veterans and service disabled veterans. Our website is www.keystoneaid7.example. We work hard to maintain a 50:50 split between veterans and non-veterans on our team. Our tagline is "To Find a Better Way." We are continually looking to integrate technology and efficiency into all that we do.

I want a way to express our company core values visually so that our employees and customers alike can read them and get a sense of who we are, what drives us to succeed, and what makes up our team DNA.

I need an artist like you to help me represent our core values visually. In a manner that I can print it out on an 8"X11" sheet of paper or a large 48" X 48" poster, without losing the visual clarity or that it pixelates out of focus. I am looking for a color scheme that is patriotic with Red, White, and Blues and similar hues. I would also like to incorporate my logo and tagline into the design in some manner.

I have attached several examples of a Core Value Grids from other companies. I am hopeful it will inspire you, and a get your brain juices flowing to provide me with a knockout Core Value Grid that will rock only you can provide! I also include a copy of my company Core Values and a copy of our Logo.

Looking forward to seeing your creations. Thanks.

Target Market(s)

Employees, any potential strategic alliance partners, and customers.

Industry/Entity Type

Contractor

Requirements
Must have
• Patriotic feel and have my logo someplace on the document.

```html
<!DOCTYPE html>
<html lang="en">
<head>
<meta charset="utf-8">
<title>Keystone Aid Partners – Core Values</title>
<link rel="stylesheet" href="https://fonts.googleapis.com/css2?family=Montserrat:wght@800&family=Maven+Pro:wght@500;600&family=Roboto:wght@400&display=swap">
<style>
  :root {
    --backdrop: #b3b3b3;
    --paper: #ffffff;
    --crimson: #a51c35;
    --maroon: #6a0f22;
    --wine: #7d1428;
    --navy: #1b2a5c;
    --ink: #2b2b2b;
    --shadow-band: #1e1b1a;
    --frame: #3a4a8a;
  }
  * { margin: 0; padding: 0; box-sizing: border-box; }
  html, body { width: 1118px; height: 1200px; overflow: hidden; }
  body { background: var(--backdrop); position: relative; font-family: "Roboto", Arial, sans-serif; }

  .sheet {
    position: absolute; left: 261px; top: 178px;
    width: 595px; height: 842px; background: var(--paper);
  }

  .header-shapes { position: absolute; left: 0; top: 0; width: 595px; height: 170px; }

  .headline {
    position: absolute; left: 26px; top: 47px;
    font-family: "Montserrat", Arial, sans-serif; font-weight: 800;
    font-size: 35px; letter-spacing: 0.5px; color: var(--paper);
  }
  .tagline {
    position: absolute; left: 191px; top: 118px; width: 404px; height: 42px;
    display: flex; align-items: center; justify-content: center;
    font-family: "Montserrat", Arial, sans-serif; font-weight: 800;
    font-size: 25px; letter-spacing: 1px; color: var(--paper);
  }

  .brand {
    position: absolute; left: 398px; top: 58px;
    display: flex; align-items: center; gap: 7px;
  }
  .brand-square { width: 16px; height: 16px; background: var(--crimson); }
  .brand-name {
    font-family: "Maven Pro", Arial, sans-serif; font-weight: 600;
    font-size: 14px; color: var(--navy); letter-spacing: 0.2px;
  }

  .value-card {
    position: absolute; border: 1px solid var(--frame); border-radius: 6px;
    background: var(--paper); padding: 0 9px;
  }
  .value-title {
    font-family: "Maven Pro", Arial, sans-serif; font-weight: 600;
    font-size: 18px; line-height: 21px; text-align: center; color: var(--maroon);
  }
  .value-title .accent { color: var(--crimson); }
  .value-text { font-size: 7.6px; line-height: 11.5px; color: var(--ink); text-align: justify; }
  .value-text p { text-indent: 9px; }
  .value-text.roomy { line-height: 12px; }
  .value-text.roomy p { margin-bottom: 3px; }

  .card-safety { left: 38px; top: 193px; width: 256px; height: 232px; }
  .card-innovation { left: 302px; top: 193px; width: 256px; height: 232px; }
  .card-wingman { left: 38px; top: 433px; width: 256px; height: 210px; }
  .card-learning { left: 302px; top: 433px; width: 256px; height: 210px; }
  .card-troops { left: 37px; top: 658px; width: 522px; height: 117px; padding: 0 13px; }

  .card-safety .value-title { margin-top: 7px; }
  .card-safety .value-text { margin-top: 13px; }
  .card-innovation .value-title { margin-top: 13px; }
  .card-innovation .value-text { margin-top: 28px; }
  .card-wingman .value-title, .card-learning .value-title { margin-top: 16px; }
  .card-wingman .value-text, .card-learning .value-text { margin-top: 16px; }
  .card-troops .value-title { margin-top: 8px; }
  .card-troops .value-text { margin-top: 9px; text-align: left; }
  .card-troops .value-text p { text-indent: 0; }

  .footer {
    position: absolute; left: 0; top: 805px; width: 595px; height: 37px;
    background: linear-gradient(90deg, var(--maroon) 0%, var(--crimson) 30%, var(--wine) 55%, var(--crimson) 78%, var(--maroon) 100%);
    display: flex; align-items: center; justify-content: center;
    color: var(--paper); font-size: 12.5px; letter-spacing: 0.3px;
  }
</style>
</head>
<body>
  <main class="sheet">
    <svg class="header-shapes" viewBox="0 0 595 170" aria-hidden="true">
      <defs>
        <linearGradient id="crimsonBand" x1="0" x2="1" y1="0" y2="0">
          <stop offset="0" stop-color="#6a0f22"/>
          <stop offset="0.55" stop-color="#a51c35"/>
          <stop offset="1" stop-color="#7d1428"/>
        </linearGradient>
      </defs>
      <polygon points="0,43 317,43 309,71 317,100 0,100" fill="url(#crimsonBand)"/>
      <polygon points="219,100 317,100 267,118 191,118" fill="var(--shadow-band)"/>
      <rect x="191" y="118" width="404" height="42" fill="var(--navy)"/>
    </svg>

    <h1 class="headline">CORE VALUES</h1>
    <div class="tagline">TO FIND A BETTER WAY</div>

    <div class="brand">
      <span class="brand-square"></span>
      <span class="brand-name">Keystone Aid Partners</span>
    </div>

    <section class="value-card card-safety">
      <h2 class="value-title">Everyone <span class="accent">comes</span> back to<br>the <span class="accent">Green Zone.</span></h2>
      <div class="value-text">
        <p>WHAT IT MEANS- Safety takes precedence over every phase of the day's operation.</p>
        <p>HOW TO EXPRESS IT - Anyone can call a stop to the work in progress if an unsafe act is occurring. In fact, it is each team member's duty to do so, rectify the unsafe issue, then proceed. Never hesitate; everyone comes back. Finally, each After Action Review begins with discussing safety issues.</p>
        <p>We always let everyone on the team know of an unsafe situation, so it can be avoided in the future.</p>
        <p>RESULT - All team members go home to their loved ones each day to pursue their individual happiness.</p>
      </div>
    </section>

    <section class="value-card card-innovation">
      <h2 class="value-title">Boldly <span class="accent">go. Seek.</span> Find.</h2>
      <div class="value-text">
        <p>WHAT IT MEANS: - We weave innovation into the fabric that makes up our company.</p>
        <p>HOW TO EXPRESS IT: - We're early adopters of technology. We quickly evaluate new technologies or processes that could separate us from our competition. Then we implement and evaluate these new technologies. We dump it quickly if we see it is not helping us achieve "Commander's Intent." We have the guts to be first. We iterate continuously and attack, attack, attack.</p>
        <p>RESULT: - We will be ahead of our competition. It' one mechanism that helps us scale. Prosperity favors the bold!</p>
      </div>
    </section>

    <section class="value-card card-wingman">
      <h2 class="value-title">Never <span class="accent">leave your</span> wingman</h2>
      <div class="value-text roomy">
        <p>WHAT IT MEANS – We always help your team members be successful. Commitment to each other and to our own personal integrity is the fuel that empowers us.</p>
        <p>HOW TO EXPRESS IT – If a Wingman is having challenges accomplishing their individual priorities or completing their assigned mission, volunteer to help them to do so.</p>
        <p>This goes for Subs/Suppliersas well. We help those who help us succeed! Always look to establish the best win-win relationship possible, and do what you can to support them if they get into a bind.</p>
        <p>RESULT – Be there for them and they will be there for us.</p>
      </div>
    </section>

    <section class="value-card card-learning">
      <h2 class="value-title">Fail <span class="accent">quickly</span> and learn</h2>
      <div class="value-text roomy">
        <p>WHAT IT MEANS – If you're not making mistakes, you're not taking enough chances or getting out of your comfort zone.</p>
        <p>HOW TO EXPRESS IT – Use your best judgment when trying something new. But, don't let your pride keep you from saying, "I was wrong" when your idea doesn't work. We trust you will know when it's time to dump the idea, or stop doing something that doesn't work.</p>
        <p>RESULT – No one will ever be penalized for making a mistake. Don't be afraid to try something you believe will work. That's how we grow ourselves and our team members.</p>
      </div>
    </section>

    <section class="value-card card-troops">
      <h2 class="value-title">Troops <span class="accent">(Team Members)</span> eat first</h2>
      <div class="value-text roomy">
        <p>WHAT IT MEANS – No leader will put themselves ahead of their subordinates.</p>
        <p>HOW TO EXPRESS IT – We lead by example. Demonstrate the moral courage and discipline to do the right thing at the highest level of quality.</p>
        <p>RESULT – Every new teammember's will quickly realize their leaders genuinely care for their welfare and success. This is the best way to drive Esprit de Corps and achieve excellence.</p>
      </div>
    </section>

    <footer class="footer">www.keystoneaid7.example</footer>
  </main>
</body>
</html>
```